Flyer, poster, banner and social media titles designs for Community Mending Chartre

The Harbourline Charter for Community Mending provide a nationally agreed framework to guide recovery policy and practice across Australia. The Principles support recovery practitioners, governments, non-government organisations and communities to deliver effective, community-centred recovery outcomes.
The Principles have recently been refreshed through extensive consultation and we require a contemporary visual identity and design suite that will increase awareness, engagement and practical application of the Principles.
The redesign will cover:
• A4 Brochure (primary publication)
• A3 Poster
• Pull up banner
• Social Media Tiles
The new design should:
• Create a recognisable brand for the Harbourline Charter.
• Appeal to both experienced and emerging recovery practitioners.
• Reflect contemporary disaster recovery practice.
• Feel people-focused rather than government-focused.
• Support future resources such as videos, implementation guides, presentations and workshop materials.
• Remain relevant for several years without requiring a major redesign.
Target Audience
• Disaster recovery practitioners
• Government agencies
• Non-government organisations
• Community recovery workers
• Recovery managers and leaders
• Community stakeholders and volunteers
The visual identity should reflect the six Principles:
• Understanding Context
• Recognising Complexity
• Community-Centred Approaches
• Coordination
• Communication
• Capacity Building
The design should communicate:
• Recovery is centred on people and communities.
• Recovery is collaborative and involves many sectors.
• Recovery is adaptive, inclusive and evidence-informed.
• Recovery supports resilience and long-term wellbeing.
• The Principles provide practical guidance for recovery practice.
We are looking for:
• Modern and professional
• Warm and approachable
• Human-centred
• Inclusive and accessible
• Australian in context
• Visually engaging
• Suitable for print and digital use
We would like to avoid:
• Images of disaster destruction
• Emergency response imagery (fire trucks, flashing lights, etc.)
• Overly corporate or bureaucratic designs
• Designs that focus on deficits rather than recovery and growth
Consider themes such as:
• Connection and collaboration
• Communities and people
• Growth, recovery and renewal
Accessibility
Designs should:
• Meet accessibility best practice
• Use clear typography
• Achieve strong colour contrast
• Be suitable for both digital and print formats

Deliverables
1. Principles Brochure
• A4 trifold size x 2 (online and print friendly version)
• A side to include cover side, logos side and overview of principles.
• B side full details of the principles
• Graphic to highlight the 3 c’s concept (RECOVERY Context, complexity, community centred, coordinate, communicate and capacity). Currently 3 circles.
• Can be printed and distributed electronically
2. Poster
• A1 and A3 versions
• Suitable for office and workshop display
3. Pull-Up Banner - 850 mm (W) × 2000 mm (H)
• Conference and event use
• High visual impact
• Strong branding and concise messaging
4. Social Media Tiles x 3

We are providing an extension and increasing the budget following feedback from designers. We are wanting the resources to look and feel different from the existing designs, considering either a different colour palette in the designs or different motif with the leave design. Any nature based designs should consider the Australian fauna or flora. Also suggest avoiding images in the designs. The principles are not numbered or liner in the concept of how they function. Happy to answer any further questions and thank you for your suggested concepts.

Disaster recovery practitioners, Government agencies , Non-government organisations, Community recovery workers and Community stakeholders and volunteers

Disaster recovery

• Modern, warm, visually engaging, human-centred, Australian in context and different to the current design.
• Symbols for each principles
• Images of disaster destruction, Emergency response imagery, Overly corporate or bureaucratic designs, Designs that focus on deficits rather than recovery and growth, avoid too much black

```html
<!DOCTYPE html>
<html lang="en">
<head>
<meta charset="utf-8">
<title>Community Mending Chartre – Brochure Spread</title>
<link rel="stylesheet" href="https://fonts.googleapis.com/css2?family=Lato:wght@400;700;900&display=swap">
<style>
:root{
  --teal:#1f5c63;
  --teal-soft:#2f7480;
  --ochre:#c9852c;
  --terracotta:#b5523b;
  --sky:#5f9fb0;
  --wattle:#e0a93a;
  --sand:#f5ecdc;
  --ink:#263238;
  --body:#3a3f42;
  --paper:#ffffff;
  --bg:#ffffff;
}
*{margin:0;padding:0;box-sizing:border-box}
html,body{width:1200px;height:498px;overflow:hidden;background:var(--bg)}
body{position:relative;font-family:"Lato",sans-serif;color:var(--body)}
.sheet{position:absolute;top:37px;width:549px;height:424px;background:var(--paper);overflow:hidden;box-shadow:0 0 2px rgba(0,0,0,.1)}
.sheet-inside{left:32px}
.sheet-outside{left:619px}
.hl{color:var(--terracotta)}
.motif{position:absolute;display:block}

/* inside spread */
.spread-title{position:absolute;top:11px;left:0;width:100%;text-align:center;font-weight:700;font-size:13px;letter-spacing:.2px;color:var(--teal)}
.spread-title .hl{color:var(--ochre)}
.principle-col{position:absolute;top:38px;width:166px}
.principle{margin-bottom:6px}
.principle-head{display:flex;gap:4px;align-items:flex-start}
.principle-icon{flex:none;width:19px;height:19px;border-radius:50%;display:flex;align-items:center;justify-content:center}
.principle-icon svg{width:11px;height:11px}
.icon-context{background:var(--teal)}
.icon-complexity{background:var(--terracotta)}
.icon-community{background:var(--ochre)}
.icon-coordinate{background:var(--sky)}
.icon-communicate{background:var(--teal-soft)}
.icon-capacity{background:var(--wattle)}
.principle-name{font-size:5.4px;font-weight:700;color:var(--ink);letter-spacing:.2px;margin-top:1px}
.principle-name .hl{color:var(--terracotta)}
.principle-lead{font-size:4.3px;line-height:6px;text-align:justify;margin-top:1.5px}
.principle-list{list-style:none;margin-top:4px}
.principle-list li{position:relative;padding-left:8px;font-size:3.7px;line-height:5.5px;margin-bottom:2.4px;text-align:justify}
.principle-list li::before{content:"";position:absolute;left:1px;top:1.6px;width:2.2px;height:2.2px;border-radius:50%;background:var(--ochre)}

/* outside spread */
.about{position:absolute;left:10px;top:7px;width:177px}
.about-title{font-size:11.5px;line-height:13px;font-weight:700;color:var(--teal);letter-spacing:.3px}
.about-title .hl{color:var(--terracotta)}
.about-text{font-size:4.5px;line-height:7.4px;text-align:justify;margin-top:8px}
.about-text+.about-text{margin-top:7px}
.success-title{position:absolute;left:10px;top:193px;font-size:10.5px;font-weight:700;color:var(--teal)}
.success-title .hl{color:var(--terracotta)}
.summary{position:absolute;top:214px;width:76px}
.summary h4{font-size:4.4px;font-weight:700;color:var(--terracotta);letter-spacing:.2px;line-height:5.6px}
.summary p{font-size:3.9px;line-height:6px;text-align:justify;margin:3px 0 5px}
.wheel{position:absolute;left:6px;top:330px;width:96px;height:90px}

.partners{position:absolute;left:187px;top:18px;width:179px;height:240px}
.partner{position:absolute;display:flex;align-items:center;gap:3px;font-size:4.6px;font-weight:700;color:var(--body);line-height:5.6px}
.partner .mark{flex:none;width:9px;height:9px;border-radius:50%;background:#d3cfc6}
.partners-title{position:absolute;left:187px;top:262px;font-size:12px;line-height:15px;font-weight:700;color:var(--teal);letter-spacing:.3px}
.partners-title .hl{color:var(--terracotta)}
.reference{position:absolute;left:187px;top:312px;font-size:6.4px;line-height:7.6px;font-weight:400}
.reference .mark{width:22px;height:22px;background:var(--sky)}

.cover{position:absolute;left:366px;top:0;width:183px;height:424px;background:var(--teal);color:#fff;overflow:hidden}
.cover-kicker{position:absolute;left:17px;top:68px;font-size:7px;letter-spacing:.2px}
.cover-brand{position:absolute;left:16px;top:78px;font-size:22px;line-height:23px;font-weight:400}
.cover-brand .hl{color:var(--wattle)}
.cover-head{position:absolute;left:17px;top:147px;font-size:19px;line-height:26px;font-weight:900;letter-spacing:.4px}
.cover-head .hl{color:var(--wattle)}
.cover-text{position:absolute;left:17px;top:232px;width:158px;font-size:9.6px;line-height:16px}
</style>
</head>
<body>

<!-- inside: full principles -->
<section class="sheet sheet-inside">
  <svg class="motif" style="left:0;top:0" width="56" height="26" viewBox="0 0 56 26" aria-hidden="true">
    <circle cx="0" cy="0" r="24" fill="none" stroke="#c9852c" stroke-width="2"/>
    <circle cx="0" cy="0" r="16" fill="none" stroke="#b5523b" stroke-width="2"/>
    <circle cx="0" cy="0" r="8" fill="#1f5c63"/>
  </svg>
  <svg class="motif" style="right:0;top:0" width="56" height="26" viewBox="0 0 56 26" aria-hidden="true">
    <circle cx="56" cy="0" r="24" fill="none" stroke="#c9852c" stroke-width="2"/>
    <circle cx="56" cy="0" r="16" fill="none" stroke="#b5523b" stroke-width="2"/>
    <circle cx="56" cy="0" r="8" fill="#1f5c63"/>
  </svg>

  <h1 class="spread-title"><span class="hl">SIX PRINCIPLES.</span> ONE SHARED PURPOSE.</h1>

  <div class="principle-col" style="left:8px">
    <div class="principle">
      <div class="principle-head">
        <span class="principle-icon icon-context"><svg viewBox="0 0 12 12"><circle cx="6" cy="6" r="4.5" fill="none" stroke="#fff" stroke-width="1"/><path d="M6 2.5 7 6 6 9.5 5 6Z" fill="#fff"/></svg></span>
        <div><div class="principle-name">UNDERSTAND THE <span class="hl">CONTEXT</span></div>
        <p class="principle-lead">Successful recovery is based on an understanding of the community context, with each community having its own history, values and dynamics. Recovery should:</p></div>
      </div>
      <ul class="principle-list">
        <li>Acknowledge existing strengths and capacity, including past experiences and future aspirations;</li>
        <li>Appreciate the risks and stressors faced by the community;</li>
        <li>Embed accessibility, equity, inclusion and diversity in recovery practice, using culturally safe and trauma-informed approaches;</li>
        <li>Support people who may be at greater risk or disproportionately impacted;</li>
        <li>Respect and support connections to Country, environment, animals and culturally significant places and recognise environmental regeneration in recovery;</li>
        <li>Recognise pathways and timeframes vary; systems should support long-term recovery shaped by community needs; and</li>
        <li>Acknowledge the impact upon the community may extend beyond the geographical boundaries where the disaster occurred.</li>
      </ul>
    </div>
    <div class="principle" style="margin-top:10px">
      <div class="principle-head">
        <span class="principle-icon icon-complexity"><svg viewBox="0 0 12 12"><path d="M6 1.5 10 3.8v4.4L6 10.5 2 8.2V3.8Z" fill="none" stroke="#fff" stroke-width="1"/><path d="M6 1.5V6l4-2.2M6 6 2 3.8M6 6v4.5" fill="none" stroke="#fff" stroke-width=".7"/></svg></span>
        <div><div class="principle-name">RECOGNISE <span class="hl">COMPLEXITY</span></div>
        <p class="principle-lead">Successful recovery is responsive to the complex and evolving nature of disasters and their impacts on communities, including compounding, cascading and concurrent events. Recovery should recognise that:</p></div>
      </div>
      <ul class="principle-list">
        <li>Disasters lead to a range of effects and impacts that require a variety of approaches; they can also leave long-term legacies;</li>
        <li>Information on impacts and needs can be limited at first and changes over time;</li>
        <li>Affected individuals and the community have diverse needs, wants and expectations, which can evolve rapidly;</li>
        <li>Responsive and flexible action is crucial to addressing immediate needs;</li>
        <li>Existing community knowledge and values may challenge the assumptions of those outside of the community;</li>
        <li>Conflicting knowledge, values and priorities among individuals, the community and organisations may create tensions;</li>
        <li>Over time, appropriate support for individuals and communities, from within and outside, can cultivate hope and individual and collective growth.</li>
      </ul>
    </div>
  </div>

  <div class="principle-col" style="left:192px">
    <div class="principle">
      <div class="principle-head">
        <span class="principle-icon icon-community"><svg viewBox="0 0 12 12"><circle cx="6" cy="4" r="1.6" fill="#fff"/><circle cx="3" cy="5.5" r="1.2" fill="#fff"/><circle cx="9" cy="5.5" r="1.2" fill="#fff"/><path d="M3.5 10a2.5 2.5 0 0 1 5 0Z" fill="#fff"/></svg></span>
        <div><div class="principle-name">USE <span class="hl">COMMUNITY-CENTRED</span> APPROACHES</div>
        <p class="principle-lead">Successful recovery is community-centred, responsive and flexible, engaging with community and supporting them to move forward, with shared responsibilities. Recovery should:</p></div>
      </div>
      <ul class="principle-list">
        <li>Assist and enable individuals, families and the community to actively participate in their own recovery;</li>
        <li>Recognise that individuals and the community may need different levels of support at various times;</li>
        <li>Be guided by the communities' priorities;</li>
        <li>Channel effort through pre-identified and existing community assets, including local knowledge, existing community strengths and resilience;</li>
        <li>Build collaborative partnerships that reflect diverse representation and community leadership in recovery;</li>
        <li>Support Aboriginal and Torres Strait Islander self-determination and Indigenous governance, recognising Country as central to recovery and resilience;</li>
        <li>Recognise that new community leaders often emerge during and after a disaster, who may not hold formal positions of authority; and</li>
        <li>Recognise that different communities may choose different paths to recovery.</li>
      </ul>
    </div>
    <div class="principle" style="margin-top:8px">
      <div class="principle-head">
        <span class="principle-icon icon-coordinate"><svg viewBox="0 0 12 12"><path d="M1.5 6.5 4 4l2 1.2L8 4l2.5 2.5L7 9.5 4.5 8Z" fill="none" stroke="#fff" stroke-width="1" stroke-linejoin="round"/></svg></span>
        <div><div class="principle-name"><span class="hl">COORDINATE</span> ALL ACTIVITIES</div>
        <p class="principle-lead">Successful recovery requires a planned, coordinated and adaptive approach, between community and partner agencies, based on continuing assessment of impacts and need. Recovery should:</p></div>
      </div>
      <ul class="principle-list">
        <li>Have clearly articulated and shared goals based on desired outcomes;</li>
        <li>Be flexible, taking into account changes in community needs or stakeholder expectations;</li>
        <li>Be guided by those with experience and expertise, using skilled, authentic and capable community leadership;</li>
        <li>Be at the pace desired by the community, and seek to collaborate and reconcile different interests and time frames;</li>
        <li>Reflect well-developed community planning and information gathering before, during and after a disaster;</li>
        <li>Have clear decision-making and reporting structures and sound governance, which are transparent and accessible to the community;</li>
        <li>Demonstrate an understanding of the roles, responsibilities and authority of organisations involved and coordinate across agencies to ensure minimal service provision disruption;</li>
        <li>Be part of an emergency management approach that integrates with response operations and contributes to future prevention and preparedness; and</li>
        <li>Be inclusive, availing of and building upon relationships created before, during and after the emergency.</li>
      </ul>
    </div>
  </div>

  <div class="principle-col" style="left:374px">
    <div class="principle">
      <div class="principle-head">
        <span class="principle-icon icon-communicate"><svg viewBox="0 0 12 12"><path d="M1.5 2.5h6v4h-4l-2 1.5Z" fill="none" stroke="#fff" stroke-width=".9"/><path d="M5 7.5h3l2 1.5V4.5H8.5" fill="none" stroke="#fff" stroke-width=".9"/></svg></span>
        <div><div class="principle-name"><span class="hl">COMMUNICATE</span> EFFECTIVELY:</div>
        <p class="principle-lead">Successful recovery is built on effective communication between the affected community and other partners. Recovery should:</p></div>
      </div>
      <ul class="principle-list">
        <li>Recognise that communication should be two-way, transparent and ongoing, building trust through shared understanding and feedback;</li>
        <li>Ensure that information is accessible to audiences in diverse situations, addresses a variety of communication needs, and is provided through a range of communication channels and networks;</li>
        <li>Establish mechanisms for coordinated and consistent communications between all service providers, organisations and individuals and the community;</li>
        <li>Ensure that all communication is relevant, timely, clear, accurate, targeted, credible and consistent; and</li>
        <li>Identify trusted sources of information and repeat key recovery messages to enable greater community confidence and receptivity.</li>
      </ul>
    </div>
    <div class="principle" style="margin-top:8px">
      <div class="principle-head">
        <span class="principle-icon icon-capacity"><svg viewBox="0 0 12 12"><rect x="2" y="7" width="1.6" height="3" fill="#fff"/><rect x="4.6" y="5.5" width="1.6" height="4.5" fill="#fff"/><rect x="7.2" y="4" width="1.6" height="6" fill="#fff"/><path d="M2 5 5 3l2 1 3-2.5" fill="none" stroke="#fff" stroke-width=".8"/></svg></span>
        <div><div class="principle-name">RECOGNISE AND BUILD <span class="hl">CAPACITY:</span></div>
        <p class="principle-lead">Successful recovery recognises, supports and builds on individual, community and organisational capacity and resilience. Recovery should:</p></div>
      </div>
      <ul class="principle-list">
        <li>Assess capability and capacity requirements before, during and after a disaster;</li>
        <li>Support the development of self-reliance, preparation and disaster mitigation;</li>
        <li>Quickly identify and mobilise community skills, strengths and resources;</li>
        <li>Develop networks and partnerships to strengthen capacity, capability and resilience;</li>
        <li>Recognise that resources can be provided by a range of partners and from community networks;</li>
        <li>Acknowledge that existing resources may be stretched, and that additional resources may be required;</li>
        <li>Understand that additional resources may only be available for a limited period, and that sustainability may need to be addressed;</li>
        <li>Understand when and how to step back, while continuing to support individuals and the community as a whole to be more self-sufficient when they are ready; and</li>
        <li>Monitor, evaluate and capture learning to strengthen future recovery and preparedness, and build resilience.</li>
      </ul>
    </div>
  </div>

  <svg class="motif" style="left:0;bottom:0" width="549" height="72" viewBox="0 0 549 72" aria-hidden="true">
    <rect x="0" y="52" width="549" height="20" fill="#f5ecdc"/>
    <g fill="none" stroke-width="6">
      <circle cx="70" cy="92" r="60" stroke="#1f5c63"/>
      <circle cx="70" cy="92" r="46" stroke="#5f9fb0"/>
      <circle cx="70" cy="92" r="32" stroke="#e0a93a"/>
      <circle cx="275" cy="100" r="72" stroke="#c9852c"/>
      <circle cx="275" cy="100" r="58" stroke="#b5523b"/>
      <circle cx="275" cy="100" r="44" stroke="#1f5c63"/>
      <circle cx="480" cy="92" r="60" stroke="#e0a93a"/>
      <circle cx="480" cy="92" r="46" stroke="#2f7480"/>
      <circle cx="480" cy="92" r="32" stroke="#b5523b"/>
    </g>
  </svg>
</section>

<!-- outside: about, partners, cover -->
<section class="sheet sheet-outside">
  <div class="about">
    <h2 class="about-title">ABOUT<br><span class="hl">DISASTER RECOVERY</span></h2>
    <p class="about-text">Disasters can deeply impact lives and livelihoods. Working with communities recovering from disasters is complex and challenging. Recovery is long-term, non-linear and dynamic, particularly in the context of compounding and concurrent disasters. These principles are a way to guide our efforts, our approach, our planning and our decision-making. Disaster recovery is part of emergency management, which includes the broader components of prevention, preparedness and response. Planning for recovery is integral to emergency preparation, and mitigation actions are often initiated as part of recovery.</p>
    <p class="about-text">Disaster recovery includes built, environmental and economic elements, as well as individual and social wellbeing. Recovery can provide an opportunity to improve these aspects beyond previous conditions, by enhancing social and natural environments, infrastructure and economies –contributing to more resilient communities. The relationship between the principles While all the principles are equally critical to ensure effective recovery, understanding the local and broader context and recognising complexity are foundational. The descriptions beneath each principle provide further guidance for working with communities in disaster recovery.</p>
  </div>
  <svg class="motif" style="left:136px;top:0" width="52" height="22" viewBox="0 0 52 22" aria-hidden="true">
    <circle cx="52" cy="0" r="20" fill="none" stroke="#c9852c" stroke-width="2"/>
    <circle cx="52" cy="0" r="13" fill="none" stroke="#b5523b" stroke-width="2"/>
    <circle cx="52" cy="0" r="6" fill="#1f5c63"/>
  </svg>

  <h2 class="success-title">SUCCESSFUL <span class="hl">RECOVERY</span></h2>
  <div class="summary" style="left:10px">
    <h4>UNDERSTAND THE CONTEXT</h4>
    <p>Successful recovery is based on an understanding of the community context, with each community having its own history, values and dynamics.</p>
    <h4>USE COMMUNITY-CENTRED APPROACHES</h4>
    <p>Successful recovery is community-centred, responsive and flexible, engaging with community and supporting them to move forward, with shared responsibilities.</p>
    <h4>COMMUNICATE EFFECTIVELY</h4>
    <p>Successful recovery is built on effective communication between the affected community and other partners.</p>
  </div>
  <div class="summary" style="left:98px">
    <h4>RECOGNISE COMPLEXITY</h4>
    <p>Successful recovery is responsive to the complex and evolving nature of disasters and their impacts on communities, including compounding, cascading and concurrent events.</p>
    <h4>COORDINATE ALL ACTIVITIES</h4>
    <p>Successful recovery requires a planned, coordinated and adaptive approach, between community and partner agencies, based on continuing assessment of impacts and needs.</p>
    <h4>RECOGNISE AND BUILD CAPACITY</h4>
    <p>Successful recovery recognises, supports and builds on individual, community and organisational capacity and resilience.</p>
  </div>

  <svg class="wheel" viewBox="0 0 96 90" aria-label="Recovery at the centre of the six principles">
    <ellipse cx="48" cy="46" rx="44" ry="38" fill="none" stroke="#1f5c63" stroke-width=".6"/>
    <circle cx="31" cy="32" r="15" fill="#c9852c"/>
    <circle cx="65" cy="32" r="15" fill="#e0a93a"/>
    <circle cx="31" cy="60" r="15" fill="#5f9fb0"/>
    <circle cx="65" cy="60" r="15" fill="#2f7480"/>
    <circle cx="48" cy="46" r="14" fill="#1f5c63" stroke="#fff" stroke-width="1.2"/>
    <text x="48" y="47.5" text-anchor="middle" font-family="Lato,sans-serif" font-size="4.8" font-weight="700" fill="#fff">RECOVERY</text>
    <g font-family="Lato,sans-serif" font-size="3.8" font-weight="700" fill="#fff" text-anchor="middle">
      <text x="27" y="29">Community</text><text x="69" y="29">Capacity</text>
      <text x="27" y="66">Coordinate</text><text x="69" y="66">Communicate</text>
    </g>
    <g font-family="Lato,sans-serif" font-size="4" fill="#263238" text-anchor="middle">
      <text x="48" y="7">Context</text><text x="48" y="89">Complexity</text>
    </g>
  </svg>

  <svg class="motif" style="left:122px;top:354px" width="244" height="70" viewBox="0 0 244 70" aria-hidden="true">
    <rect x="0" y="50" width="244" height="20" fill="#f5ecdc"/>
    <g fill="none" stroke-width="6">
      <circle cx="170" cy="100" r="76" stroke="#c9852c"/>
      <circle cx="170" cy="100" r="62" stroke="#b5523b"/>
      <circle cx="170" cy="100" r="48" stroke="#1f5c63"/>
      <circle cx="170" cy="100" r="34" stroke="#e0a93a"/>
    </g>
  </svg>

  <div class="partners">
    <div class="partner" style="left:6px;top:20px"><span class="mark"></span>Commonwealth Office of<br>Community Services</div>
    <div class="partner" style="left:92px;top:20px"><span class="mark"></span>Commonwealth Office<br>of Civic Affairs</div>
    <div class="partner" style="left:0;top:80px"><span class="mark"></span>Southern Relief<br>Network</div>
    <div class="partner" style="left:62px;top:80px"><span class="mark"></span>Gulfland<br>Regional Council</div>
    <div class="partner" style="left:122px;top:80px"><span class="mark"></span>Westcoast<br>Regional Council</div>
    <div class="partner" style="left:0;top:134px"><span class="mark"></span>Islandia<br>Regional Council</div>
    <div class="partner" style="left:62px;top:134px"><span class="mark"></span>Sunreach<br>Regional Council</div>
    <div class="partner" style="left:122px;top:134px"><span class="mark"></span>Capital District<br>Council</div>
    <div class="partner" style="left:0;top:185px"><span class="mark"></span>Topend<br>Regional Council</div>
    <div class="partner" style="left:70px;top:185px"><span class="mark"></span>Southvale<br>Regional Council</div>
    <div class="partner" style="left:0;top:225px"><span class="mark"></span>Eastshore Office of<br>Recovery Coordination</div>
  </div>
  <h2 class="partners-title"><span class="hl">PARTNERS IN</span><br>DEVELOPMENT FROM THE</h2>
  <div class="partner reference"><span class="mark"></span>Community Mending<br>Reference Circle</div>

  <div class="cover">
    <svg class="motif" style="right:0;top:0" width="90" height="60" viewBox="0 0 90 60" aria-hidden="true">
      <g fill="none" stroke="#2f7480" stroke-width="3">
        <circle cx="90" cy="0" r="56"/><circle cx="90" cy="0" r="44"/><circle cx="90" cy="0" r="32"/><circle cx="90" cy="0" r="20"/>
      </g>
    </svg>
    <p class="cover-kicker">HARBOURLINE CHARTER FOR</p>
    <h1 class="cover-brand">Community<br><span class="hl">Mending</span></h1>
    <svg class="motif" style="left:126px;top:100px" width="57" height="34" viewBox="0 0 57 34" aria-hidden="true">
      <circle cx="57" cy="34" r="30" fill="none" stroke="#e0a93a" stroke-width="3"/>
      <circle cx="57" cy="34" r="20" fill="none" stroke="#c9852c" stroke-width="3"/>
      <circle cx="57" cy="34" r="10" fill="#b5523b"/>
    </svg>
    <h2 class="cover-head">PEOPLE AT<br>THE <span class="hl">HEART OF</span><br><span class="hl">RECOVERY</span></h2>
    <p class="cover-text">The Harbourline Charter for Community Mending provide a nationally agreed framework to guide recovery policy and practice across Australia.</p>
    <svg class="motif" style="left:0;bottom:0" width="183" height="80" viewBox="0 0 183 80" aria-hidden="true">
      <g fill="none" stroke="#2f7480" stroke-width="3">
        <circle cx="40" cy="110" r="90"/><circle cx="40" cy="110" r="74"/><circle cx="40" cy="110" r="58"/>
        <circle cx="160" cy="120" r="70"/><circle cx="160" cy="120" r="54"/>
      </g>
    </svg>
  </div>
</section>

</body>
</html>
```